Professional Photography Business cards

I need business cards that include my logo which I have uploaded. I run a photography business. I am open to ideas but I would like one side to have my logo and the other side to have my contact info. I don't have a website made but I do own a website domain. I have uploaded 2 different logo color schemes. My business colors are Blue, black , and white.

Business Name
Business Phone Number
Business Email
Business Website address
Instagram

Industry/Entity Type

Professional Photography

Contact Information for Business Card

Phone Number: 916-384-7702 email: info@tlane-studio.example Instagram: @t.lanestudio website doman- www.tlane-studio.example

Requirements
Must have
• I like the idea of a business card with a full black background front and back of card. My colors must include royal blue, black, and white

```html
<!DOCTYPE html>
<html lang="en">
<head>
<meta charset="utf-8">
<title>T. Lane Studio – Business Cards</title>
<link href="https://fonts.googleapis.com/css2?family=Roboto:wght@300;400&display=swap" rel="stylesheet">
<style>
  :root {
    --page-bg: #000000;
    --card-bg: #2c2d30;
    --card-stripe: #303134;
    --ink-white: #ffffff;
    --royal-blue: #1f2ad0;
    --divider: #8a8b8f;
  }
  * { box-sizing: border-box; margin: 0; padding: 0; }
  html, body {
    width: 1200px; height: 900px; overflow: hidden;
    background: var(--page-bg);
    font-family: "Roboto", Arial, sans-serif;
  }
  .stage { position: relative; width: 1200px; height: 900px; }
  .card {
    position: absolute;
    width: 458px; height: 282px;
    border-radius: 13px;
    background:
      repeating-linear-gradient(90deg, var(--card-bg) 0 2px, var(--card-stripe) 2px 4px);
    overflow: hidden;
  }
  .card--back { left: 138px; top: 265px; }
  .card--front { left: 625px; top: 268px; }

  /* contact side */
  .brand-small {
    position: absolute; left: 16px; top: 112px; width: 190px;
    color: var(--ink-white);
  }
  .brand-small__name {
    display: flex; align-items: center; justify-content: space-between;
    white-space: nowrap;
    font-weight: 400; font-size: 21px; line-height: 1;
  }
  .brand-small__dot {
    width: 36px; height: 36px; border: 2.5px solid var(--ink-white); border-radius: 50%;
    flex: none;
  }
  .brand-small__tag {
    margin-top: 10px; text-align: right; padding-right: 6px;
    font-size: 7px; letter-spacing: 4.2px; font-weight: 400;
  }
  .divider {
    position: absolute; left: 217px; top: 102px; width: 1px; height: 78px;
    background: var(--divider);
  }
  .contact-list {
    position: absolute; left: 231px; top: 98px; list-style: none;
    color: var(--ink-white); font-size: 14px; font-weight: 400;
  }
  .contact-list li { display: flex; align-items: center; gap: 6px; height: 17px; white-space: nowrap; }
  .contact-list li.social { margin-top: 12px; height: 20px; }
  .contact-list svg { width: 12px; height: 12px; flex: none; }
  .social-mark {
    width: 14px; height: 14px; border: 1.5px solid var(--ink-white); border-radius: 50%;
    flex: none; margin-right: 2px;
  }

  /* logo side */
  .brand-large {
    position: absolute; left: 50px; top: 84px; width: 358px;
  }
  .brand-large__name {
    display: flex; align-items: center; justify-content: space-between;
    white-space: nowrap;
    color: var(--royal-blue); font-weight: 400; font-size: 40px; line-height: 1;
  }
  .brand-large__dot {
    width: 84px; height: 84px; border: 5px solid var(--ink-white); border-radius: 50%;
    flex: none;
  }
  .brand-large__tag {
    margin-top: 14px; text-align: right; padding-right: 4px;
    color: var(--ink-white);
    font-size: 12px; letter-spacing: 9.6px; font-weight: 400;
  }
</style>
</head>
<body>
<main class="stage">
  <section class="card card--back" aria-label="Contact side">
    <div class="brand-small">
      <div class="brand-small__name">T. Lane Studio<span class="brand-small__dot"></span></div>
      <div class="brand-small__tag">PHOTOGRAPHY</div>
    </div>
    <div class="divider"></div>
    <ul class="contact-list">
      <li>
        <svg viewBox="0 0 24 24" fill="none" stroke="#fff" stroke-width="2.2" aria-hidden="true"><path d="M5 3h4l2 5-2.5 1.5a11 11 0 0 0 6 6L16 13l5 2v4a2 2 0 0 1-2 2A17 17 0 0 1 3 5a2 2 0 0 1 2-2z"/></svg>
        916-384-7702
      </li>
      <li>
        <svg viewBox="0 0 24 24" fill="none" stroke="#fff" stroke-width="2.2" aria-hidden="true"><rect x="2" y="5" width="20" height="14"/><path d="M2 5l10 8 10-8M2 19l7-7M22 19l-7-7"/></svg>
        info@tlane-studio.example
      </li>
      <li>
        <svg viewBox="0 0 24 24" fill="none" stroke="#fff" stroke-width="2" aria-hidden="true"><circle cx="12" cy="12" r="10"/><ellipse cx="12" cy="12" rx="4.5" ry="10"/><path d="M2 12h20M4 7h16M4 17h16"/></svg>
        www.tlane-studio.example
      </li>
      <li class="social"><span class="social-mark"></span>@t.lanestudio</li>
    </ul>
  </section>

  <section class="card card--front" aria-label="Logo side">
    <div class="brand-large">
      <div class="brand-large__name">T. Lane Studio<span class="brand-large__dot"></span></div>
      <div class="brand-large__tag">PHOTOGRAPHY</div>
    </div>
  </section>
</main>
</body>
</html>
```